New B2C website design to help dads be better dads

DadHarbor is a website to help dads be the “best dad you can be.”

We require our website to be designed into a PSD format, no coding necessary.

The general concept is a two-page design. The first page is the login page, the second page is the home page. Once at the home page, rather than navigating to and from different pages, the user will push and pull through different visual and functional layers of the hierarchy. In theory, this should add to the user experience by having a visual anchor of where they are (through layered pagination) as well as improving loading times since the new information should only be a delta in data load versus a brand new page load.

The general look-and-feel we are going for is clean, simple, minimal. This means that the winning design will show us a good eye for web-optimized typography, good use of white (negative) space, and good use of a visually pleasing grid.

We require a total of 6 page "views" plus the landing page. We note that many of the views are similar to one another.
Landing page
Milestone view
Task view
Content view, articles
Content view, products
Search view
What's new view

Please review all of the additional information provided as well as the attachments for examples.

We provide the following websites as good references for:

Typography:
http://example-kelvorn.com/journal/

Use of white space:
http://www.trenvaskit.com/
http://moldrefin.com/

Example for “scrolling” page concept as well as good balance of color, typography, and white space:
http://www.qorbitalmeet.eu/

Please contact us with questions so that we can guide your design effort.
Updates

Hello designers,

The following information is added to help guide the design process:

1.  For the text dialogue below the landing page, please assume the following word count:
"why are we making dad harbor?": 250 words
"who are we?" 200 words
"what's the deal with the penguin logo?" 300 words

For the social media links, please see http://www.gravelplumbs.com/
Notice the floating "social" bar that is always to the right.  This is the concept we are going for, please try to implement this as you see fit. 

Target Market(s)

Fathers of young children ages 0-6 years old.

Industry/Entity Type

Product

Font styles to use
Sans Serif

Requirements
Must have
• Clean lines, minimal design concept

Incorporation of our logo (see attached document)

Header content is static for all views after landing page, see example

This page WILL be responsive, please keep that in mind when designing
The timeline bar should be to the left, with the timeline bar’s “milestones” also being responsive.

Designer is free to suggest font types, but any fonts used must be royalty-free and web-optimized. We request a minimum number of font types as well as fonts that load relatively fast. We reinforce that visually appealing typography is a significant factor in the winning design choice.

While we are not expecting the winning design to include code, please keep in mind that the final implementation needs to be optimized for desktop, tablet, and mobile platforms.

If you are using stock photography that is not generated by you, please provide where/how we can obtain imagery, as well as price.

All custom graphics must be available in original formats; Photoshop/GIMP layered files for layout design, and vector formats for logos, icons and other graphical elements.

Please incorporate “Blue” into design elements as you see fit, as the RGB 67 74 169 Blue is the primary color used in our brand. The complement to this blue is 255 202 0, a brownish orange. Feel free to use this color as well, although please keep it to a lesser amount.

Background color is your choice, do not feel the need to use the grey.
Should not have
• Excessive graphical content such that it affects loading times

Excessive use of too many font types such that it affects loading times

```html
<!DOCTYPE html>
<html lang="en">
<head>
<meta charset="utf-8">
<title>DadHarbor – Home</title>
<link rel="stylesheet" href="https://fonts.googleapis.com/css2?family=Source+Sans+3:wght@400;600&family=Noto+Serif:wght@400&display=swap">
<style>
:root{
  --brand-blue:#434aa9;
  --brand-gold:#ffca00;
  --heading-gold:#d49a1e;
  --ink:#444;
  --ink-soft:#666;
  --muted:#888;
  --line:#d8d8d8;
  --page:#f6f6f6;
  --card:#fff;
  --star:#f5c000;
}
*{box-sizing:border-box;margin:0;padding:0}
html,body{width:848px;height:1200px;overflow:hidden}
body{background:var(--page);font-family:"Source Sans 3",Arial,sans-serif;color:var(--ink);position:relative}

.site-header{position:absolute;left:0;top:0;width:848px;height:132px;background:#fff;border-bottom:1px solid var(--line)}
.brand{position:absolute;left:70px;top:88px;display:flex;align-items:center;gap:8px;font-size:20px;font-weight:600;color:var(--brand-blue);letter-spacing:.3px}
.brand-dot{width:14px;height:14px;border-radius:50%;background:var(--brand-blue)}
.welcome{position:absolute;right:70px;top:12px;font-family:"Noto Serif",Georgia,serif;font-size:19px;color:var(--heading-gold)}
.search{position:absolute;left:497px;top:54px;display:flex;gap:6px}
.search-input{width:216px;height:25px;border:1px solid #d5d5d5;background:#fff;font-size:10px;color:#999;padding:6px 10px}
.search-btn{width:54px;height:25px;background:var(--brand-gold);border:1px solid #e6a800;color:#8a5a00;font-size:11px;font-weight:600;display:flex;align-items:center;justify-content:center}
.account-bar{position:absolute;left:497px;top:98px;width:275px;display:flex;align-items:center;font-size:11.5px}
.score{color:var(--brand-blue);display:flex;align-items:center;gap:6px}
.account-links{margin-left:auto;color:var(--muted)}
.account-links span{margin:0 5px}

.timeline{position:absolute;left:70px;top:150px;width:1px;height:970px;background:var(--line)}
.milestone{position:absolute;left:40px;display:flex;align-items:center}
.milestone-age{width:24px;font-size:9px;color:var(--muted);text-align:right;margin-right:6px}
.milestone-node{width:9px;height:9px;border-radius:50%;background:#555;position:relative}
.milestone-node::after{content:"";position:absolute;left:3px;top:2px;border:2.5px solid transparent;border-left:3px solid #fff}
.milestone-title{font-family:"Noto Serif",Georgia,serif;color:#555;margin-left:14px}
.rule{position:absolute;left:70px;width:708px;height:1px;background:var(--line)}

.sort{position:absolute;left:640px;top:156px;display:flex;align-items:center;gap:6px;font-size:9.5px;color:var(--muted)}
.sort-select{width:97px;height:20px;border:1px solid #ccc;background:#fff;font-size:9.5px;color:#444;padding:3px 7px;position:relative}
.sort-select::after{content:"";position:absolute;right:7px;top:8px;border:3.5px solid transparent;border-top:4px solid #555}

.task-list{position:absolute;left:93px;top:260px;width:172px;height:258px;background:#fff;border:1px solid var(--line);border-top:none;list-style:none;padding:3px 6px}
.task{height:31px;display:flex;align-items:center;border-bottom:1px solid #eee;font-size:11px;color:#444;padding-left:12px}
.task:last-child{border-bottom:none}
.task-box{width:8px;height:8px;border:1px solid #aaa;margin-right:9px;background:#f4f4f4;position:relative}
.task-box.done::after{content:"";position:absolute;left:2px;top:0;width:2px;height:4px;border:solid var(--brand-blue);border-width:0 1.2px 1.2px 0;transform:rotate(40deg)}

.related-title{position:absolute;left:278px;width:497px;top:279px;text-align:center;font-family:"Noto Serif",Georgia,serif;font-size:14.5px;color:#444}
.card{position:absolute;width:238px;height:265px;background:var(--card);border:1px solid var(--line);padding:4px}
.card-media{height:128px;position:relative}
.card-badge{position:absolute;right:2px;bottom:2px;width:27px;height:27px;background:var(--brand-gold);display:flex;align-items:center;justify-content:center}
.card-body{padding:10px 8px 0}
.card-title{font-family:"Noto Serif",Georgia,serif;font-size:11.5px;line-height:16px;color:var(--brand-blue)}
.rating{display:flex;align-items:center;gap:1px;margin-top:7px;font-size:10px;color:var(--ink-soft)}
.rating span{margin-left:8px}
.card-text{margin-top:9px;font-size:9.8px;line-height:16px;color:var(--ink-soft)}
.read-more{color:var(--brand-blue);display:inline-flex;align-items:center;gap:3px;margin-left:4px}

.footer-rule{position:absolute;left:0;top:1198px;width:848px;height:1px;background:var(--line)}
</style>
</head>
<body>
<svg width="0" height="0" style="position:absolute">
  <defs>
    <symbol id="star" viewBox="0 0 20 20"><path d="M10 1l2.7 5.9 6.3.6-4.8 4.2 1.4 6.3L10 14.8 4.4 18l1.4-6.3L1 7.5l6.3-.6z" fill="#f5c000"/></symbol>
    <symbol id="star-half" viewBox="0 0 20 20"><path d="M10 1l2.7 5.9 6.3.6-4.8 4.2 1.4 6.3L10 14.8 4.4 18l1.4-6.3L1 7.5l6.3-.6z" fill="#ddd"/><path d="M10 1v13.8L4.4 18l1.4-6.3L1 7.5l6.3-.6z" fill="#f5c000"/></symbol>
    <symbol id="doc" viewBox="0 0 16 18"><path d="M3 1h10v16H3z" fill="#111"/><path d="M1 3h10v14H1z" fill="#111" stroke="#ffca00" stroke-width="1"/></symbol>
    <symbol id="cart" viewBox="0 0 20 16"><path d="M1 2h3l2 9h10l2-7H5" fill="none" stroke="#111" stroke-width="1.8"/><circle cx="8" cy="14" r="1.4" fill="#111"/><circle cx="15" cy="14" r="1.4" fill="#111"/></symbol>
    <symbol id="more" viewBox="0 0 10 10"><circle cx="5" cy="5" r="5" fill="#434aa9"/><path d="M5 2.5v5M2.5 5h5" stroke="#fff" stroke-width="1.4"/></symbol>
  </defs>
</svg>

<header class="site-header">
  <div class="brand"><span class="brand-dot"></span>DadHarbor</div>
  <h1 class="welcome">Welcome Aldo, what would you like to do today?</h1>
  <div class="search">
    <div class="search-input">Keyword...</div>
    <div class="search-btn">SEARCH</div>
  </div>
  <div class="account-bar">
    <div class="score"><svg width="10" height="9" viewBox="0 0 10 9"><path d="M5 9L1 5A2.3 2.3 0 015 1.6 2.3 2.3 0 019 5z" fill="#434aa9"/></svg>Super Dad Score: 10,500</div>
    <div class="account-links">My Account<span>|</span>Log out</div>
  </div>
</header>

<div class="timeline"></div>

<div class="milestone" style="top:160px"><span class="milestone-age">-3 mo</span><span class="milestone-node"></span><span class="milestone-title" style="font-size:17px">Prepare for the baby arrival</span></div>
<div class="sort">Sort by :<div class="sort-select">Most recent</div></div>
<div class="rule" style="top:200px"></div>

<div class="milestone" style="top:220px"><span class="milestone-age">0 mo</span><span class="milestone-node"></span><span class="milestone-title" style="font-size:14.5px">What’s the Latest?</span></div>
<div class="rule" style="top:260px"></div>

<ul class="task-list">
  <li class="task"><span class="task-box"></span>Buy a crib</li>
  <li class="task"><span class="task-box"></span>Assemble the crib</li>
  <li class="task"><span class="task-box"></span>Buy a stroller</li>
  <li class="task"><span class="task-box done"></span>Buy a carseat</li>
  <li class="task"><span class="task-box"></span>Install a carseat</li>
  <li class="task"><span class="task-box"></span>Learn to change a diaper</li>
  <li class="task"><span class="task-box"></span>Learn to hold a baby</li>
  <li class="task"><span class="task-box"></span>Set a fedding schedule</li>
</ul>

<div class="milestone" style="top:552px"><span class="milestone-age">0 mo</span><span class="milestone-node"></span><span class="milestone-title" style="font-size:14.5px">What you searched for</span></div>

<h2 class="related-title">Related milestones and tasks include</h2>

<!-- Cards -->
<article class="card" style="left:278px;top:310px">
  <div class="card-media" role="img" aria-label="Photo of a baby in a car seat playing with a toy" style="background:linear-gradient(135deg,#6e7480,#3a3d45 60%,#9aa0aa)"><div class="card-badge"><svg width="14" height="16"><use href="#doc"/></svg></div></div>
  <div class="card-body">
    <h3 class="card-title">Pellentesque habitant morbi tristique senectus et netus</h3>
    <div class="rating"><svg width="14" height="14"><use href="#star"/></svg><svg width="14" height="14"><use href="#star"/></svg><svg width="14" height="14"><use href="#star"/></svg><svg width="14" height="14"><use href="#star"/></svg><svg width="14" height="14"><use href="#star-half"/></svg><span>3,121 ratings</span></div>
    <p class="card-text">I went out to buy my first car seat and had to earn my PhD in car seats, Newtonian physics, and anti-stain technology···<span class="read-more"><svg width="9" height="9"><use href="#more"/></svg>Read More</span></p>
  </div>
</article>

<article class="card" style="left:538px;top:310px">
  <div class="card-media" role="img" aria-label="Photo of a smiling baby in an infant carrier" style="background:linear-gradient(135deg,#b5a592,#6b5b4c 55%,#cfc7bd)"><div class="card-badge"><svg width="18" height="15"><use href="#cart"/></svg></div></div>
  <div class="card-body">
    <h3 class="card-title">Pellentesque habitant morbi tristique senectus et netus</h3>
    <div class="rating"><svg width="14" height="14"><use href="#star"/></svg><svg width="14" height="14"><use href="#star"/></svg><svg width="14" height="14"><use href="#star"/></svg><svg width="14" height="14"><use href="#star"/></svg><svg width="14" height="14"><use href="#star-half"/></svg><span>3,121 ratings</span></div>
    <p class="card-text">I went out to buy my first car seat and had to earn my PhD in car seats, Newtonian physics, and anti-stain technology···<span class="read-more"><svg width="9" height="9"><use href="#more"/></svg>Read More</span></p>
  </div>
</article>

<article class="card" style="left:278px;top:598px">
  <div class="card-media" role="img" aria-label="Photo of a toddler buckled into a car seat" style="background:linear-gradient(135deg,#c79868,#8a4e30 50%,#3b3f66)"><div class="card-badge"><svg width="14" height="16"><use href="#doc"/></svg></div></div>
  <div class="card-body">
    <h3 class="card-title">Pellentesque habitant morbi tristique senectus et netus</h3>
    <div class="rating"><svg width="14" height="14"><use href="#star"/></svg><svg width="14" height="14"><use href="#star"/></svg><svg width="14" height="14"><use href="#star"/></svg><svg width="14" height="14"><use href="#star"/></svg><svg width="14" height="14"><use href="#star-half"/></svg><span>3,121 ratings</span></div>
    <p class="card-text">I went out to buy my first car seat and had to earn my PhD in car seats, Newtonian physics, and anti-stain technology···<span class="read-more"><svg width="9" height="9"><use href="#more"/></svg>Read More</span></p>
  </div>
</article>

<article class="card" style="left:538px;top:598px">
  <div class="card-media" role="img" aria-label="Product photo of an infant car seat with a baby" style="background:linear-gradient(90deg,#3e4145,#55585c 50%,#3e4145)"><div class="card-badge"><svg width="18" height="15"><use href="#cart"/></svg></div></div>
  <div class="card-body">
    <h3 class="card-title">Pellentesque habitant morbi tristique senectus et netus</h3>
    <div class="rating"><svg width="14" height="14"><use href="#star"/></svg><svg width="14" height="14"><use href="#star"/></svg><svg width="14" height="14"><use href="#star"/></svg><svg width="14" height="14"><use href="#star"/></svg><svg width="14" height="14"><use href="#star-half"/></svg><span>3,121 ratings</span></div>
    <p class="card-text">I went out to buy my first car seat and had to earn my PhD in car seats, Newtonian physics, and anti-stain technology···<span class="read-more"><svg width="9" height="9"><use href="#more"/></svg>Read More</span></p>
  </div>
</article>

<article class="card" style="left:278px;top:886px">
  <div class="card-media" role="img" aria-label="Photo of a baby strapped in a car seat belt" style="background:linear-gradient(135deg,#7c8a95,#5d6b75 50%,#a9b6bd)"><div class="card-badge"><svg width="14" height="16"><use href="#doc"/></svg></div></div>
  <div class="card-body">
    <h3 class="card-title">Pellentesque habitant morbi tristique senectus et netus</h3>
    <div class="rating"><svg width="14" height="14"><use href="#star"/></svg><svg width="14" height="14"><use href="#star"/></svg><svg width="14" height="14"><use href="#star"/></svg><svg width="14" height="14"><use href="#star"/></svg><svg width="14" height="14"><use href="#star-half"/></svg><span>3,121 ratings</span></div>
    <p class="card-text">I went out to buy my first car seat and had to earn my PhD in car seats, Newtonian physics, and anti-stain technology···<span class="read-more"><svg width="9" height="9"><use href="#more"/></svg>Read More</span></p>
  </div>
</article>

<article class="card" style="left:538px;top:886px">
  <div class="card-media" role="img" aria-label="Photo of a sleeping newborn in a car seat" style="background:linear-gradient(135deg,#4a3a30,#c7b6a8 50%,#3a2c24)"><div class="card-badge"><svg width="18" height="15"><use href="#cart"/></svg></div></div>
  <div class="card-body">
    <h3 class="card-title">Pellentesque habitant morbi tristique senectus et netus</h3>
    <div class="rating"><svg width="14" height="14"><use href="#star"/></svg><svg width="14" height="14"><use href="#star"/></svg><svg width="14" height="14"><use href="#star"/></svg><svg width="14" height="14"><use href="#star"/></svg><svg width="14" height="14"><use href="#star-half"/></svg><span>3,121 ratings</span></div>
    <p class="card-text">I went out to buy my first car seat and had to earn my PhD in car seats, Newtonian physics, and anti-stain technology···<span class="read-more"><svg width="9" height="9"><use href="#more"/></svg>Read More</span></p>
  </div>
</article>

<div class="footer-rule"></div>
</body>
</html>
```